Business Landing Page for SEO Company

Need the landing page of the website designed - I will provide the copy, will need to include details of my company and the services offered, about us, testimonials, faq, etc., and all these elements will need to be arranged graphically on the page.

I want something similar to this: https://torvanequill.com/

Not in terms of color or theme or anything, but we offer a similar service and want to display similar information.

Th services we provide are:

Premium Links
Monthly Links Subscription
Link Insertions

Need to advertise them on the front page. Additionally need a place for testimonials, company details, etc.,

We already have logo for the website. Please use the attached file to insert the logo within the overal design.

Target Market(s)

SEO marketers and agencies

Number of Pages Required

1 page

```html
<!DOCTYPE html>
<html lang="en">
<head>
<meta charset="utf-8">
<title>Linkwell – Link Building Services</title>
<link href="https://fonts.googleapis.com/css2?family=Poppins:wght@400;500;600;700&display=swap" rel="stylesheet">
<style>
:root{
  --blue:#3a86e0;
  --blue-dark:#2c74cf;
  --orange:#f28c1c;
  --ink:#1d1d2b;
  --muted:#5b5f6b;
  --soft:#f4f8fd;
  --line:#d9e3ef;
  --backdrop:#eef0f3;
}
*{box-sizing:border-box;margin:0;padding:0}
html,body{width:1200px;height:4232px;overflow:hidden}
body{background:var(--backdrop);font-family:'Poppins',sans-serif;color:var(--ink)}
.page{position:absolute;left:163px;top:67px;width:866px;height:3949px;background:#fff;box-shadow:0 6px 30px rgba(0,0,0,.08);overflow:hidden}
.abs{position:absolute}
.center{text-align:center}
.eyebrow{font-size:10px;font-weight:500;letter-spacing:.3px;color:var(--ink)}
.h2{font-size:21px;font-weight:600;color:var(--ink)}
.rule{height:2px;width:64px;background:var(--orange)}
.body{font-size:10.5px;line-height:20px;color:var(--muted)}

/* header */
.header{left:0;top:0;width:866px;height:58px;background:#fff}
.brand{font-weight:500;color:var(--ink);font-size:18px;white-space:nowrap}
.nav{left:258px;top:24px;display:flex;gap:16px;font-size:8.5px;font-weight:500;color:var(--ink)}
.btn-outline{border:1.5px solid var(--blue);color:var(--blue);font-size:9px;font-weight:500;border-radius:3px;display:flex;align-items:center;justify-content:center}
.btn{background:var(--blue);color:#fff;font-size:10px;font-weight:500;border-radius:3px;display:flex;align-items:center;justify-content:center;box-shadow:0 4px 10px rgba(58,134,224,.3)}

/* hero */
.hero{left:0;top:58px;width:866px;height:350px;background:linear-gradient(160deg,#3b8ae6 0%,#2f7bd8 60%,#3d8de4 100%)}
.hero h1{position:absolute;top:82px;width:100%;text-align:center;color:#fff;font-size:30px;font-weight:600}
.hero h1 span{color:var(--orange)}
.hero p{position:absolute;top:132px;left:163px;width:540px;text-align:center;color:#e5effc;font-size:10.5px;line-height:19px}
.svc{top:306px;width:221px;height:196px;background:#fff;box-shadow:0 8px 24px rgba(20,40,80,.12);text-align:center}
.svc .ic{width:45px;height:45px;border-radius:50%;border:1.5px solid #b8d3f3;margin:14px auto 0;display:flex;align-items:center;justify-content:center}
.svc h3{font-size:12px;font-weight:500;color:var(--blue);margin-top:16px}
.svc p{font-size:9px;line-height:20px;color:var(--muted);padding:6px 18px 0}
.svc a{display:block;font-size:8px;color:var(--orange);margin-top:8px;text-decoration:none}

.art{border-radius:8px}

/* features */
.feat{left:472px;width:340px;display:flex;gap:12px}
.feat .ic{flex:none;width:34px;height:34px;border-radius:50%;background:var(--blue);display:flex;align-items:center;justify-content:center}
.feat h4{font-size:11.5px;font-weight:500;margin-bottom:4px}
.feat p{font-size:8.5px;line-height:20px;color:var(--muted)}

/* testimonials */
.band{left:0;width:866px;background:var(--soft)}
.tcard{top:1474px;width:220px;height:192px;background:#fff;box-shadow:0 4px 16px rgba(20,40,80,.07);text-align:center}
.tcard .avatar{position:absolute;left:24px;top:-14px;width:45px;height:45px;border-radius:50%;background:linear-gradient(#9aa6b6,#4e5a6b)}
.tcard .quote{position:absolute;right:22px;top:4px;font-size:34px;font-weight:700;color:#d7dbe2;line-height:1}
.tcard p{font-size:9.5px;line-height:20px;color:var(--muted);padding:44px 20px 0}
.tcard .stars{color:var(--orange);font-size:9px;letter-spacing:3px;margin-top:6px}
.tcard .who{color:var(--blue);font-size:9.5px}
.dots{left:0;width:866px;top:1697px;display:flex;justify-content:center;gap:9px}
.dots i{width:4px;height:4px;border-radius:50%;background:#b8c0cc}
.dots i:first-child{background:var(--orange);width:5px;height:5px}

/* blog */
.post{top:2269px;width:210px;height:208px;background:#fff;box-shadow:0 4px 16px rgba(20,40,80,.08)}
.post .ph{height:104px}
.post p{font-size:9.5px;line-height:17px;text-align:center;color:var(--ink);padding:14px 14px 0}

/* faq */
.faq{left:157px;top:2672px;width:552px;height:405px;background:#fff;border-radius:26px;box-shadow:0 6px 24px rgba(20,40,80,.1)}
.faq .open{position:absolute;left:60px;top:26px;width:460px}
.faq .open h4{font-size:12px;font-weight:500}
.faq .open p{font-size:10px;line-height:15px;color:var(--muted);margin-top:8px}
.qa{left:43px;width:474px;height:35px;border-radius:18px;background:#fff;box-shadow:0 2px 10px rgba(20,40,80,.1);display:flex;align-items:center;justify-content:space-between;padding:0 12px 0 28px;font-size:10px}
.qa i{width:14px;height:14px;border-radius:50%;background:var(--blue);color:#fff;font-style:normal;font-size:11px;line-height:14px;text-align:center}

/* partners */
.partner{top:3258px;width:117px;height:75px;border:1px solid #e3e7ee;display:flex;align-items:center;justify-content:center}
.partner span{display:block;width:58px;height:16px;background:#2a2a33;border-radius:2px}

/* consult */
.consult{left:0;top:3365px;width:866px;height:352px;background:#f5f6f8}
.field{left:458px;width:284px;height:34px;border:1px solid #c7ccd4;background:#fff;font-size:8px;color:#8a909b;padding:12px 16px}
.contact{left:90px;font-size:9px;color:var(--muted);display:flex;gap:10px;align-items:flex-start;line-height:13px}

/* footer */
.footer{left:0;top:3717px;width:866px;height:232px;background:var(--soft)}
.fh{font-size:13px;font-weight:500}
.ftext{font-size:9.5px;line-height:18px;color:var(--ink)}
.soc{top:81px;width:12px;height:12px;border-radius:2px;background:var(--ink)}
.copy{left:0;width:866px;top:216px;text-align:center;font-size:8px;color:var(--muted)}
</style>
</head>
<body>
<main class="page">

  <header class="abs header">
    <div class="abs brand" style="left:74px;top:17px">Linkwell</div>
    <nav class="abs nav"><span>GUEST POSTS</span><span>NICHE EDITS</span><span>TIERED LINKS</span><span>TIERED LINKS</span><span>BACKLINK PACKAGES</span></nav>
    <div class="abs btn-outline" style="left:704px;top:16px;width:90px;height:26px">Get In Touch</div>
  </header>

  <section class="abs hero">
    <h1>Boost Sale With <span>Linkwell</span></h1>
    <p>Lorem ipsum dolor sit amet, consectetur adipiscing elit. Sollicitudin turpis metus placerat cursus nisl tortor placerat. Id ornare in consequat suspendisse sed nunc bibendum arcu nunc. Tortor turpis metus ultrices sem tincidunt sit justo.</p>
  </section>

  <article class="abs svc" style="left:63px">
    <div class="ic"><svg width="22" height="22" viewBox="0 0 24 24" fill="none" stroke="#3a86e0" stroke-width="1.5"><rect x="3" y="4" width="18" height="14" rx="1"/><path d="M6 15l4-4 3 3 5-6"/></svg></div>
    <h3>Premium Links</h3>
    <p>Lorem ipsum dolor sit amet, consectetur adipiscing elit. Phasellus dolor nec, urna nulla amet, in orci.</p>
    <a href="#">Learn More</a>
  </article>
  <article class="abs svc" style="left:322px">
    <div class="ic"><svg width="22" height="22" viewBox="0 0 24 24" fill="none" stroke="#3a86e0" stroke-width="1.5"><path d="M10 14a4 4 0 0 0 6 0l3-3a4 4 0 0 0-6-6l-1 1"/><path d="M14 10a4 4 0 0 0-6 0l-3 3a4 4 0 0 0 6 6l1-1"/></svg></div>
    <h3>Monthly Links Subscription</h3>
    <p>Lorem ipsum dolor sit amet, consectetur adipiscing elit. Phasellus dolor nec, urna nulla amet, in orci.</p>
    <a href="#">Learn More</a>
  </article>
  <article class="abs svc" style="left:582px">
    <div class="ic"><svg width="22" height="22" viewBox="0 0 24 24" fill="none" stroke="#3a86e0" stroke-width="1.5"><path d="M4 11h4v9H4zM8 19h9l3-7h-6l1-6-2-1-5 7"/></svg></div>
    <h3>Link Insertions</h3>
    <p>Lorem ipsum dolor sit amet, consectetur adipiscing elit. Phasellus dolor nec, urna nulla amet, in orci.</p>
    <a href="#">Learn More</a>
  </article>

  <div class="abs eyebrow" style="left:70px;top:622px">ABOUT US</div>
  <h2 class="abs h2" style="left:70px;top:638px">Who We Are?</h2>
  <div class="abs rule" style="left:70px;top:667px;width:140px"></div>
  <p class="abs body" style="left:70px;top:683px;width:285px">Lorem ipsum dolor sit amet, consectetur adipiscing elit. Amet tellus arcu leo orci. Nec nibh non praesent et varius. Diam amet sed diam pretium eleifend eget id. Massa nisi ultrices integer nunc congue et vel est. Sed vitae senectus nam etiam porttitor sem id. Lacus risus malesuada accumsan ut.</p>
  <div class="abs btn" style="left:70px;top:824px;width:103px;height:32px">Learn More</div>
  <div class="abs art" role="img" aria-label="Illustration of three team members with a laptop surrounded by contact and location icons" style="left:381px;top:629px;width:440px;height:264px;background:linear-gradient(135deg,#e8f1fc,#f9e9b8 55%,#dcebfb)"></div>

  <div class="abs art" role="img" aria-label="Illustration of two monitors joined by a chain with a megaphone and play button" style="left:58px;top:992px;width:342px;height:253px;background:linear-gradient(135deg,#e6e8ee,#fbc93a 45%,#f46a55 75%,#23337a)"></div>

  <div class="abs feat" style="top:1010px">
    <div class="ic"><svg width="16" height="16" viewBox="0 0 24 24" fill="none" stroke="#fff" stroke-width="2"><rect x="3" y="4" width="18" height="14" rx="1"/><path d="M6 15l4-4 3 3 5-6"/></svg></div>
    <div><h4>Quality Over Quantity</h4><p>Forget the days of being penalised for spammy links. We only deliver the highest quality links. Every link we use for you is a link we would use on our own sites.</p></div>
  </div>
  <div class="abs feat" style="top:1112px">
    <div class="ic"><svg width="16" height="16" viewBox="0 0 24 24" fill="none" stroke="#fff" stroke-width="2"><path d="M10 14a4 4 0 0 0 6 0l3-3a4 4 0 0 0-6-6l-1 1"/><path d="M14 10a4 4 0 0 0-6 0l-3 3a4 4 0 0 0 6 6l1-1"/></svg></div>
    <div><h4>One Off Link Payments</h4><p>All our links are one off payments. We believe you should pay once and not worry about continual link rental payments building up.</p></div>
  </div>
  <div class="abs feat" style="top:1214px">
    <div class="ic"><svg width="16" height="16" viewBox="0 0 24 24" fill="none" stroke="#fff" stroke-width="2"><path d="M4 11h4v9H4zM8 19h9l3-7h-6l1-6-2-1-5 7"/></svg></div>
    <div><h4>Lifetime Link Guarantee</h4><p>All of our links are guaranteed for life. Don't worry about any of your links that you order dropping off.</p></div>
  </div>

  <section class="abs band" style="top:1333px;height:413px"></section>
  <div class="abs eyebrow center" style="left:0;width:866px;top:1363px">TESTIMONIAL</div>
  <h2 class="abs h2 center" style="left:0;width:866px;top:1382px">Happy Clients Say It All</h2>
  <div class="abs rule" style="left:373px;top:1417px;width:120px"></div>

  <article class="abs tcard" style="left:70px"><div class="avatar" role="img" aria-label="Client portrait"></div><span class="quote">”</span><p>Lorem ipsum dolor sit amet, consectetur adipiscing elit. Neque maecenas egestas morbi sed amet, scelerisque. In eu at sit augue lectus semper ut in.</p><div class="stars">★★★★★</div><div class="who">Marcus Delaney</div></article>
  <article class="abs tcard" style="left:317px"><div class="avatar" role="img" aria-label="Client portrait"></div><span class="quote">”</span><p>Lorem ipsum dolor sit amet, consectetur adipiscing elit. Neque maecenas egestas morbi sed amet, scelerisque. In eu at sit augue lectus semper ut in.</p><div class="stars">★★★★★</div><div class="who">Marcus Delaney</div></article>
  <article class="abs tcard" style="left:565px"><div class="avatar" role="img" aria-label="Client portrait"></div><span class="quote">”</span><p>Lorem ipsum dolor sit amet, consectetur adipiscing elit. Neque maecenas egestas morbi sed amet, scelerisque. In eu at sit augue lectus semper ut in.</p><div class="stars">★★★★★</div><div class="who">Marcus Delaney</div></article>
  <div class="abs dots"><i></i><i></i><i></i><i></i></div>

  <div class="abs" role="img" aria-label="Faint world map backdrop" style="left:230px;top:1760px;width:420px;height:330px;background:radial-gradient(ellipse at center,#f1f3f6 0%,rgba(255,255,255,0) 70%)"></div>
  <h2 class="abs h2 center" style="left:0;width:866px;top:1837px">Our UK Based Agency Has Years Of Experience &amp; Testing</h2>
  <div class="abs rule" style="left:366px;top:1870px;width:134px"></div>
  <p class="abs body center" style="left:100px;width:666px;top:1899px;color:var(--ink)">We’ve been refining our off-page SEO strategy over the past 4 years, figuring out what works and what doesn’t.</p>
  <p class="abs body center" style="left:100px;width:666px;top:1939px;color:var(--ink)">This means that with our link campaigns all you have to do is check that you’re happy with the anchor texts and target URLs we’ve chosen. So, you can focus on other areas of your business, whether that’s lead generation or on-page SEO.</p>
  <p class="abs body center" style="left:100px;width:666px;top:1998px;color:var(--ink)">Based in the United Kingdom (UK), we are continually testing and tweaking to make sure that we are at the forefront of link building techniques.</p>
  <div class="abs btn-outline" style="left:341px;top:2069px;width:173px;height:32px;font-size:10px">Start Free Consulation</div>

  <div class="abs eyebrow center" style="left:0;width:866px;top:2177px">LATEST BLOG</div>
  <h2 class="abs h2 center" style="left:0;width:866px;top:2192px">Our Case Studies</h2>
  <div class="abs rule" style="left:358px;top:2226px;width:150px"></div>

  <article class="abs post" style="left:67px"><div class="ph" role="img" aria-label="Photo of a hand holding a card with a chain link against a building" style="background:linear-gradient(135deg,#1f3c68,#8fb5de 60%,#e8eef6)"></div><p>Link Building Budget: How Much Should You Spend on Link Building?</p></article>
  <article class="abs post" style="left:320px"><div class="ph" role="img" aria-label="Photo of a hand touching a glowing global network" style="background:linear-gradient(135deg,#c8d2de,#8a96a6 50%,#d68a3c 70%,#e3e7ec)"></div><p>Foreign Link Building: Can You Build English Links In Foreign SERPs?</p></article>
  <article class="abs post" style="left:571px"><div class="ph" role="img" aria-label="Photo of a laptop showing a website optimization screen" style="background:linear-gradient(135deg,#26354d,#9aa8b9 55%,#dfe5ec)"></div><p>Link Velocity: Maintain Stronger Rankings Than 90% of SEOs</p></article>
  <div class="abs btn" style="left:365px;top:2514px;width:120px;height:32px">See More Blog</div>

  <section class="abs band" style="top:2594px;height:536px"></section>
  <h2 class="abs h2 center" style="left:0;width:866px;top:2623px">FAQ</h2>
  <div class="abs faq">
    <div class="open"><h4>How much do the cooking kits cost?</h4><p>We offer 3 subscription plans: monthly, 6-month, and 12-month subscriptions. The monthly subscription is $15/month. Our 6-month subscription is an upfront payment of $84 ($14/month).</p></div>
    <div class="abs qa" style="top:122px">Do you send food?<i>+</i></div>
    <div class="abs qa" style="top:176px">What ages are your cooking kits appropiate for?<i>+</i></div>
    <div class="abs qa" style="top:230px">What will I receive each month?<i>+</i></div>
    <div class="abs qa" style="top:284px">How quickly will I receive my first kit after placing my order?<i>+</i></div>
    <div class="abs qa" style="top:340px">How do you address food allergies?<i>+</i></div>
  </div>

  <h2 class="abs h2 center" style="left:0;width:866px;top:3180px">Trusted Partner</h2>
  <p class="abs center" style="left:0;width:866px;top:3214px;font-size:11.5px;color:var(--ink)">Lorem ipsum, or lipsum as it is sometimes known,</p>
  <div class="abs partner" style="left:93px"><span></span></div>
  <div class="abs partner" style="left:232px"><span></span></div>
  <div class="abs partner" style="left:373px"><span></span></div>
  <div class="abs partner" style="left:514px"><span></span></div>
  <div class="abs partner" style="left:653px"><span></span></div>

  <section class="abs consult">
    <h2 class="abs h2" style="left:90px;top:62px">Gets Free Consulation</h2>
    <p class="abs" style="left:90px;top:102px;width:320px;font-size:11px;line-height:18px;color:#7a7f89">Lorem ipsum dolor sit amet, consectetur adipiscing elit. Lobortis sodales integer risus semper at dignissim egestas. Netus in adipiscing ut phasellus porttitor justo, ac. Amet, diam lacus, eros, ut sit mattis placerat. Cras ultricies mi, semper diam consequat varius urna mauris at. Leo urna nulla orci quam lectus.</p>
    <div class="abs contact" style="top:258px"><svg width="12" height="10" viewBox="0 0 24 20" fill="none" stroke="#1d1d2b" stroke-width="2"><rect x="1" y="1" width="22" height="18"/><path d="M1 1l11 9 11-9"/></svg>mara.voss@linkwell.com</div>
    <div class="abs contact" style="top:282px"><svg width="10" height="13" viewBox="0 0 20 26" fill="none" stroke="#1d1d2b" stroke-width="2"><path d="M10 25s8-9 8-15a8 8 0 0 0-16 0c0 6 8 15 8 15z"/><circle cx="10" cy="10" r="3"/></svg><span>214 Harbor Lane, Fairview,<br>Oregon 97024 United States</span></div>
    <div class="abs field" style="top:46px">Write your name</div>
    <div class="abs field" style="top:96px">Write your email</div>
    <div class="abs field" style="top:145px">Write web url</div>
    <div class="abs field" style="top:195px;height:70px">Write your message</div>
    <div class="abs btn" style="left:458px;top:285px;width:84px;height:24px;font-size:9px">Submit</div>
  </section>

  <footer class="abs footer">
    <div class="abs fh" style="left:67px;top:45px">About Us</div>
    <p class="abs ftext" style="left:67px;top:76px;width:160px">Lorem ipsum dolor sit amet, consectetur adipiscing elit. Lobortis sodales integer risus semper at dignissim egestas.</p>
    <div class="abs fh" style="left:282px;top:45px">Our Services</div>
    <div class="abs ftext" style="left:282px;top:74px;line-height:22.5px">Email Marketing<br>Premium Links<br>Monthly Links Subscription<br>Link Insertions</div>
    <div class="abs fh" style="left:469px;top:45px">Follow us</div>
    <span class="abs soc" style="left:477px"></span>
    <span class="abs soc" style="left:506px"></span>
    <span class="abs soc" style="left:536px"></span>
    <span class="abs soc" style="left:565px"></span>
    <div class="abs brand" style="left:632px;top:62px;font-size:30px">Linkwell</div>
    <div class="abs copy">Copyright 2021 - Linkwell. All right reserved</div>
  </footer>

</main>
</body>
</html>
```